A parent Company needs a website as a leading diversified business in industrial Conglomerates in Af

Velkor Group is a private (Holding) limited liability company incorporated under the Companies Code, 1963 (Act 179) in November, 2013 to following the speedy growth in numbers of its current subsidiaries which has been founded several years ago with an emerging force to become one of the largest and a leading diversified business in industrial Conglomerates in Africa.
The Group which is 100% wholly owned indigenous Ghanaian Company focuses on provision of local, value-added products and services that meet the needs of the African population. The Group is headquartered in Accra, Ghana with interests across a range of sectors in Africa.
We are currently into Food & Beverage, Real Estate Development, Transportation, Health Care, Consumer Products Distribution, Agro Processing, Manufacturing, ICT, Exports & Import, and still counting.
In the next 3 years, we shall announce our ambitions to enter Ghana's largest Oil and Gas industry, playing a strategic role in the petroleum sector with strategic alliances, and help build Ghana's biggest and most important Energy sector in the country.
Inspired by billionaires Tom Prewitt, Harlan Voskel, and Emeka Ofodile, Velkor Group (Velkor Foundation) is committed to making a name for itself on the philanthropic circuit and has given away privately and still given to the cause to the needy in the society and some specific social causes in Ghana.
The company is managed by a 5 member board and a 2 member advisory experts who are non-board members.
The company has a vision, mission and it is guided by its core values.
We would like to see a designs that is very professional and looks corporate and can attract investors and partners. It must communicate financial safety and growth and must reflect our logo colors.

```html
<!DOCTYPE html>
<html lang="en">
<head>
<meta charset="utf-8">
<title>Velkor Group</title>
<link href="https://fonts.googleapis.com/css2?family=PT+Sans:wght@400;700&family=Ubuntu:wght@400;500;700&display=swap" rel="stylesheet">
<style>
:root{
  --blue:#1a9ad6;
  --blue-dark:#0f7fb8;
  --blue-light:#2fb3ea;
  --ink:#222;
  --text:#555;
  --muted:#777;
  --page:#f3f3f3;
  --dark:#2e2e2e;
  --footer:#141414;
  --line:#d6d6d6;
  --white:#fff;
}
*{margin:0;padding:0;box-sizing:border-box}
html,body{width:826px;height:1200px;overflow:hidden}
body{position:relative;background:var(--page);font-family:"PT Sans",sans-serif;color:var(--text)}
.abs{position:absolute}
.top-rule{left:0;top:0;width:826px;height:2px;background:#444}

/* header */
.brand{left:76px;top:26px;display:flex;align-items:center;gap:6px}
.brand-dot{width:16px;height:16px;border-radius:50%;background:var(--blue)}
.brand-name{font-family:"Ubuntu",sans-serif;font-weight:500;font-size:13px;color:var(--ink);letter-spacing:.3px}
.search{left:600px;top:29px;width:150px;height:19px;background:#333;border:1px solid #222;border-radius:2px;color:#999;font-size:8px;font-style:italic;padding:4px 5px}

/* nav */
.main-nav{left:76px;top:70px;width:674px;height:31px;background:linear-gradient(#28abe6,#1389c6);display:flex;align-items:center;padding-left:9px;gap:0;z-index:3;box-shadow:0 1px 2px rgba(0,0,0,.2)}
.main-nav a{color:var(--white);text-decoration:none;font-family:"Ubuntu",sans-serif;font-weight:700;font-size:10px;margin-right:21px;display:flex;align-items:center;gap:3px;text-shadow:0 1px 0 rgba(0,0,0,.25)}
.main-nav svg{width:9px;height:9px;fill:#fff}

/* hero */
.hero{left:0;top:84px;width:826px;height:346px;background:linear-gradient(160deg,#3f6fa8 0%,#8fb3d9 40%,#c9a26b 62%,#a8753e 100%)}
.hero-title{left:78px;top:188px;width:198px;height:38px;background:rgba(30,30,30,.88);color:#fff;font-family:"Ubuntu",sans-serif;font-weight:700;font-size:20px;padding:8px 10px;letter-spacing:.3px}
.hero-text{left:76px;top:236px;width:287px;height:80px;background:rgba(30,30,30,.82);color:#fff;font-size:10.5px;line-height:15px;padding:10px 15px;font-weight:700}
.btn{display:inline-block;background:var(--blue);color:#fff;font-size:8px;padding:5px 8px;border-radius:2px;font-family:"PT Sans",sans-serif;font-weight:400}
.hero-text .btn{margin-top:7px}
.slide-arrow{top:218px;width:27px;height:43px;background:#111;display:flex;align-items:center;justify-content:center}
.slide-arrow svg{width:10px;height:10px;fill:none;stroke:#fff;stroke-width:3}

/* features band */
.band{left:0;top:455px;width:826px;height:72px;border-top:1px solid var(--line);border-bottom:1px solid var(--line)}
.feature{top:466px;display:flex;gap:8px}
.feature-num{width:34px;height:31px;background:#1d1d1d;color:#fff;font-family:"Ubuntu",sans-serif;font-size:17px;display:flex;align-items:center;justify-content:center;flex:none}
.feature h3{font-family:"Ubuntu",sans-serif;font-weight:400;font-size:11.5px;color:var(--blue);line-height:12px}
.feature p{font-size:7.5px;line-height:10px;color:var(--muted);width:115px}
.feature .more{font-size:7.5px;color:#333;margin-top:4px}

/* welcome */
.welcome{left:84px;top:547px;width:410px}
.welcome h1{font-family:"Ubuntu",sans-serif;font-weight:400;font-size:19px;color:#111}
.welcome h1 span{color:var(--blue)}
.welcome p{font-size:8px;line-height:16px;color:#666;margin-top:3px}
.welcome .more{font-size:8px;color:#222;margin-top:4px}
.social{left:588px;top:553px}
.social h2{font-family:"Ubuntu",sans-serif;font-weight:400;font-size:12px;color:var(--blue)}
.social p{font-size:7.5px;color:#666;margin-top:6px}
.social-row{display:flex;gap:5px;margin-top:12px}
.social-row span{width:17px;height:17px;background:#fff;border:1px solid #ddd;display:flex;align-items:center;justify-content:center}
.social-row span i{width:7px;height:7px;border-radius:50%;background:#555}

/* dividers */
.divider{left:90px;width:646px;height:24px}

/* services */
.services-head{left:90px;top:706px;width:646px;height:20px}
.services-title{left:101px;top:707px;font-family:"Ubuntu",sans-serif;font-size:14px;color:var(--blue);background:var(--page);padding:0 4px}
.services-rule{left:186px;top:715px;width:510px;height:4px;background:repeating-linear-gradient(45deg,#ccc 0 1px,transparent 1px 3px)}
.pager{top:709px;width:15px;height:15px;display:flex;align-items:center;justify-content:center}
.pager svg{width:7px;height:7px;fill:none;stroke:#fff;stroke-width:2}
.card{top:743px;width:198px;height:197px;box-shadow:0 4px 4px -2px rgba(0,0,0,.25)}
.card-head{height:52px;background:var(--dark);display:flex;align-items:center;gap:8px;padding:10px 14px 0;color:#fff;font-family:"Ubuntu",sans-serif;font-weight:500;font-size:12px;position:relative}
.card-head::after{content:"";position:absolute;top:0;left:96px;border:4px solid transparent;border-top-color:#fff}
.card-head svg{width:22px;height:22px;fill:#fff}
.card-img{height:145px}

/* footer */
.footer{left:0;top:1028px;width:826px;height:172px;background:var(--footer);border-top:4px solid #333}
.to-top{left:396px;top:1016px;width:34px;height:34px;border-radius:50%;background:#555;display:flex;align-items:center;justify-content:center}
.to-top svg{width:12px;height:12px;fill:none;stroke:#fff;stroke-width:3}
.foot-about{left:91px;top:1053px;width:240px;color:#bbb}
.foot-about h3{font-family:"Ubuntu",sans-serif;font-weight:400;font-size:12px;color:#fff;display:flex;align-items:center;gap:8px}
.foot-about h3 i{width:22px;height:22px;border-radius:50%;background:#777;display:block}
.foot-about p{font-size:8px;line-height:15.2px;margin-top:11px}
.foot-about p span{color:var(--blue-light)}
.foot-about .btn{margin-top:8px;font-size:9px;padding:5px 9px;background:var(--blue-light)}
.foot-col{top:1067px;color:#bbb}
.foot-col h3{font-family:"Ubuntu",sans-serif;font-weight:500;font-size:12px;color:#fff;margin-bottom:9px}
.foot-col li{list-style:none;font-size:8px;line-height:15.2px}
.copy{right:75px;top:1175px;font-size:8px;color:#aaa}
</style>
</head>
<body>
<div class="abs top-rule"></div>

<header>
  <div class="abs brand"><span class="brand-dot"></span><span class="brand-name">VELKOR GROUP</span></div>
  <div class="abs search">Search..</div>
  <nav class="abs main-nav">
    <a href="#"><svg viewBox="0 0 10 10"><path d="M5 1 0 5h1.5v4h2.5V6h2v3h2.5V5H10z"/></svg>HOME</a>
    <a href="#"><svg viewBox="0 0 10 10"><rect x="0" y="2" width="10" height="2"/><rect x="0" y="5" width="10" height="3"/></svg>FOOD</a>
    <a href="#"><svg viewBox="0 0 10 10"><path d="M5 0a3 3 0 0 0-3 3c0 2 3 7 3 7s3-5 3-7a3 3 0 0 0-3-3z"/></svg>REAL ESTATE DEVELOPMENT</a>
    <a href="#"><svg viewBox="0 0 10 10"><rect x="0" y="2" width="6" height="5"/><path d="M6 4h2.5L10 6v1H6z"/><circle cx="2" cy="8" r="1"/><circle cx="8" cy="8" r="1"/></svg>TRANSPORTATION</a>
    <a href="#"><svg viewBox="0 0 10 10"><circle cx="5" cy="3" r="2.5"/><path d="M0 10c0-3 2-4.5 5-4.5s5 1.5 5 4.5z"/></svg>MANUFACTURING</a>
  </nav>
</header>

<section>
  <div class="abs hero" role="img" aria-label="Construction worker in a hard hat building a timber roof frame against a blue sky"></div>
  <div class="abs hero-title">MANUFACTURING</div>
  <div class="abs hero-text">We have products for everyone, whether you are concerned with price, speed or both<br><span class="btn">Read More</span></div>
  <div class="abs slide-arrow" style="left:0"><svg viewBox="0 0 10 10"><path d="M7 1 3 5l4 4"/></svg></div>
  <div class="abs slide-arrow" style="left:799px"><svg viewBox="0 0 10 10"><path d="M3 1l4 4-4 4"/></svg></div>
</section>

<section>
  <div class="abs band"></div>
  <div class="abs feature" style="left:76px"><div class="feature-num">1</div><div><h3>FOOD</h3><p>Lorem Ipsum is simply dummy text of the printing</p></div></div>
  <div class="abs feature" style="left:243px"><div class="feature-num">2</div><div><h3>ESTATE DEVELOPMENT</h3><p>Lorem Ipsum is simply dummy text of the printing</p><div class="more">Read More</div></div></div>
  <div class="abs feature" style="left:427px"><div class="feature-num">3</div><div><h3>TRANSPORTATION</h3><p>Lorem Ipsum is simply dummy text of the printing</p><div class="more">Read More</div></div></div>
  <div class="abs feature" style="left:597px"><div class="feature-num">4</div><div><h3>MANUFACTURING</h3><p>Lorem Ipsum is simply dummy text of the printing</p><div class="more">Read More</div></div></div>
</section>

<section>
  <div class="abs welcome">
    <h1>Welcome to <span>VELKOR GROUP</span></h1>
    <p>Lorem Ipsum is simply dummy text of the printing and typesetting industry. Lorem Ipsum has been the industry's standard dummy text ever since the 1500s, when an unknown printer took a galley of type and scrambled it to make a type specimen book. It has survived not only five centuries, but also the leap into electronic typesetting,</p>
    <div class="more">Read More</div>
  </div>
  <div class="abs social">
    <h2>Get Socialize On</h2>
    <p>Morbi vitae neque lectus, a venenatis felis.</p>
    <div class="social-row"><span><i></i></span><span><i></i></span><span><i></i></span><span><i></i></span><span><i></i></span><span><i></i></span><span><i></i></span></div>
  </div>
</section>

<svg class="abs divider" style="top:666px" viewBox="0 0 646 24"><line x1="0" y1="12" x2="646" y2="12" stroke="#d0d0d0"/><line x1="268" y1="8" x2="378" y2="8" stroke="#d0d0d0"/><line x1="268" y1="16" x2="378" y2="16" stroke="#d0d0d0"/><rect x="315" y="4" width="16" height="16" transform="rotate(45 323 12)" fill="#f3f3f3" stroke="#aaa" stroke-width="3"/></svg>

<section>
  <div class="abs services-rule"></div>
  <div class="abs services-title">Our Services</div>
  <div class="abs pager" style="left:697px;background:#999"><svg viewBox="0 0 8 8"><path d="M5 1 2 4l3 3"/></svg></div>
  <div class="abs pager" style="left:713px;background:#222"><svg viewBox="0 0 8 8"><path d="M3 1l3 3-3 3"/></svg></div>

  <div class="abs card" style="left:94px">
    <div class="card-head"><svg viewBox="0 0 24 24"><path d="M4 2h1.5v7h1V2H8v7h1V2h1.5v8c0 1.5-1 2.5-2 2.5V22H6v-9.5c-1 0-2-1-2-2.5zM15 2c3 0 4 4 4 8h-2v12h-2.5z"/></svg>FOOD</div>
    <div class="card-img" role="img" aria-label="Basket of fruit, sandwiches and cookies" style="background:linear-gradient(135deg,#7a3a22,#c98a3a 50%,#6b8a2a)"></div>
  </div>
  <div class="abs card" style="left:314px">
    <div class="card-head"><svg viewBox="0 0 24 24"><rect x="1" y="5" width="13" height="11"/><path d="M15 9h4l4 4v3h-8z"/><circle cx="5" cy="18" r="2.5"/><circle cx="18" cy="18" r="2.5"/></svg>TRANSPORTATION</div>
    <div class="card-img" role="img" aria-label="Blue lorry driving across a bridge" style="background:linear-gradient(160deg,#c98ad0,#6a5ab8 45%,#2a3a8a)"></div>
  </div>
  <div class="abs card" style="left:535px">
    <div class="card-head"><svg viewBox="0 0 24 24"><path d="M1 22V6h3v6l5-4v4l5-4v4l5-4V2h3v20z"/></svg>MANUFACTURING</div>
    <div class="card-img" role="img" aria-label="Crane beside a steel building frame under construction" style="background:linear-gradient(180deg,#e8eef3,#c0a89a 60%,#8a6a5a)"></div>
  </div>
</section>

<svg class="abs divider" style="top:969px" viewBox="0 0 646 24"><line x1="0" y1="12" x2="646" y2="12" stroke="#d0d0d0"/><line x1="268" y1="8" x2="378" y2="8" stroke="#d0d0d0"/><line x1="268" y1="16" x2="378" y2="16" stroke="#d0d0d0"/><rect x="315" y="4" width="16" height="16" transform="rotate(45 323 12)" fill="#f3f3f3" stroke="#aaa" stroke-width="3"/></svg>

<footer>
  <div class="abs footer"></div>
  <div class="abs to-top"><svg viewBox="0 0 12 12"><path d="M2 8l4-4 4 4"/></svg></div>
  <div class="abs foot-about">
    <h3><i></i>Become a customer today!</h3>
    <p><span>Lorem Ipsum</span> is simply dummy text of the printing and type-setting industry. Lorem Ipsum has been the industry's standard dummy text ever since the 1500s, when an unknown printer took a galley of type and scrambled</p>
    <span class="btn">Be contacted by a customer consultant</span>
  </div>
  <div class="abs foot-col" style="left:415px">
    <h3>PRODUCTS</h3>
    <ul><li>Home</li><li>Food</li><li>Real Estate Development</li><li>Transportation</li><li>Manufacturing</li></ul>
  </div>
  <div class="abs foot-col" style="left:597px">
    <h3>CONTACT US</h3>
    <ul><li>Call us weekdays 10:00 to 3:00 p.m.</li><li>55 41 27 90</li><li>Or send e-mail on post@velkorgroup.com</li></ul>
  </div>
  <div class="abs copy">Copyright 2014 © Velkor Group All Rights Reserved</div>
</footer>
</body>
</html>
```